goal design

We are rolling out a goal for the next 3 years. the goal is as follows:
2014: $8 million gross profit, $1.25 million net income
2015: $12 million gross profit, $2.4 million net income
2016 $15 million gross profit, $4 million net income
We want a design that captures these numbers and that we can publish company wide that will quickly remind everyone of these goals. Our website is www.brackenfieldcrew.com. This will be an internal campaign. We will use the simple design to remind our people of our goals for the next 3 years. We will print it on mouse pads, shirts and things of this nature periodically to keep it front of mind for our people. So easy to remember, visually appealing and simple are good guidelines.
Updates
Target Market(s)
This is an internal campaign. it is to remind our people of our goals for the next few years so will be on little reminder items (i.e. cell phone covers, mouse pads, shirts, screen savers, etc).
Industry/Entity Type
It Company
Look and feel

```html
<!DOCTYPE html>
<html lang="en">
<head>
<meta charset="utf-8">
<title>Three-Year Goals 2014–2016</title>
<link rel="stylesheet" href="https://fonts.googleapis.com/css2?family=Archivo:wght@700;800;900&family=Oswald:wght@600&family=Roboto+Condensed:wght@700&display=swap">
<style>
  :root {
    --paper: #ffffff;
    --steel-blue: #7aa0c5;
    --navy: #0e3e6b;
    --label-navy: #0d3a66;
    --text-light: #ffffff;
  }
  html, body {
    margin: 0;
    padding: 0;
    width: 1200px;
    height: 999px;
    overflow: hidden;
    background: var(--paper);
  }
  .goal-poster {
    display: block;
    width: 1200px;
    height: 999px;
  }
  .year-tag {
    font-family: "Archivo", Arial, sans-serif;
    font-weight: 900;
    font-size: 30px;
    fill: var(--label-navy);
    letter-spacing: 0.5px;
  }
  .goal-lines {
    font-family: "Archivo", Arial, sans-serif;
    font-weight: 700;
    font-size: 17px;
    fill: var(--text-light);
  }
  .arrow-year {
    font-family: "Oswald", "Arial Narrow", sans-serif;
    font-weight: 600;
    font-size: 50px;
    fill: var(--text-light);
  }
  .arrow-lines {
    font-family: "Roboto Condensed", "Arial Narrow", sans-serif;
    font-weight: 700;
    font-size: 16px;
    fill: var(--text-light);
  }
  .box-2014 { fill: var(--steel-blue); }
  .growth-arrow { fill: var(--steel-blue); }
  .box-2015 { fill: var(--navy); }
</style>
</head>
<body>
<svg class="goal-poster" viewBox="0 0 800 666" xmlns="http://www.w3.org/2000/svg" role="img" aria-label="Goals: 2014 $8 million gross profit, $1.25 million net income; 2015 $12 million gross profit, $2.4 million net income; 2016 $15 million gross profit, $4 million net income">
  <!-- 2014 step -->
  <text class="year-tag" transform="translate(188 446) rotate(-90)">2014</text>
  <rect class="box-2014" x="190" y="351" width="138" height="94"/>
  <text class="goal-lines" x="199" y="376">
    <tspan x="199">$8 million</tspan>
    <tspan x="199" dy="17.5">gross profit</tspan>
    <tspan x="199" dy="17.5">$1.25 million</tspan>
    <tspan x="199" dy="17.5">net income</tspan>
  </text>

  <!-- 2016 growth arrow -->
  <path class="growth-arrow"
        d="M469 298 L553 220 L637 298 L603 298 L603 400
           C603 430 590 445 560 445 L480 445 L470 351 Z"/>

  <!-- 2015 step -->
  <text class="year-tag" transform="translate(360 446) rotate(-90)">2015</text>
  <path class="box-2015"
        d="M363 351 L468 351 C492 351 500 385 503 420
           C505 436 515 445 525 445 L363 445 Z"/>
  <text class="goal-lines" x="371" y="376">
    <tspan x="371">$12 million</tspan>
    <tspan x="371" dy="17.5">gross profit</tspan>
    <tspan x="371" dy="17.5">$2.4 million</tspan>
    <tspan x="371" dy="17.5">netincome</tspan>
  </text>

  <!-- 2016 labels -->
  <text class="arrow-year" x="553" y="299" text-anchor="middle">2016</text>
  <text class="arrow-lines" text-anchor="middle">
    <tspan x="553" y="332">$15 million</tspan>
    <tspan x="553" dy="20">gross profit</tspan>
    <tspan x="553" dy="20">$4 million</tspan>
    <tspan x="553" dy="20">net income</tspan>
  </text>
</svg>
</body>
</html>
```